TEBSIRK HOA Portal Site for Public

Clean up and organize current website; need website to look good and functional; this is a HOA (homeowner association management) website where homeowners can login and pay their bill, general information about a HOA, monthly newsletter page.
Competitors:
https://quillmarsh.example/
https://dorvinpalms.example/
https://www.kelbrookhomes.example/nevada
http://www.tpw-hoa.example/

Target Market(s)

homeowners

Industry/Entity Type

Real Estate

Coding

Coded - Design and coding required

Number of Pages Required

5+ page

Font styles to use
Serif

Colors
0292cd
33a6d7
e667a6
e34297

Requirements
Must have
• login to pay
• services page
• contact us
• order resale package
Nice to have
• page why an HOA would contract us

```html
<!DOCTYPE html>
<html lang="en">
<head>
<meta charset="utf-8">
<title>TEBSIRK HOA</title>
<link rel="stylesheet" href="https://fonts.googleapis.com/css2?family=Marcellus&family=Mulish:wght@400;600&display=swap">
<style>
:root{
  --blue:#0292cd;
  --blue-light:#33a6d7;
  --pink-light:#e667a6;
  --pink:#e34297;
  --text:#555;
  --dark:#333;
  --field:#f1f1f1;
  --serif:"Marcellus", serif;
  --sans:"Mulish", sans-serif;
}
*{margin:0;padding:0;box-sizing:border-box}
html,body{width:1200px;height:3125px;overflow:hidden;background:#fff}
body{position:relative;font-family:var(--sans);color:var(--text)}
.abs{position:absolute}
.topbar{left:0;top:0;width:1200px;height:93px;background:linear-gradient(var(--blue-light),var(--blue))}
.brand{left:80px;top:26px;font-family:var(--serif);font-size:30px;color:#fff;letter-spacing:.5px;white-space:nowrap}
.phone-badge{left:952px;top:22px;width:46px;height:46px;border-radius:50%;background:var(--pink-light);display:flex;align-items:center;justify-content:center}
.phone-num{left:1015px;top:34px;font-size:15px;color:#fff;white-space:nowrap}
.nav-bar{left:0;top:93px;width:1200px;height:51px;background:#fff;border-bottom:1px solid #e5e5e5}
.nav-home{left:89px;top:87px;width:77px;height:67px;background:var(--pink-light);clip-path:polygon(0 0,100% 0,100% 88%,50% 100%,0 88%)}
.nav-link{position:absolute;top:111px;font-size:13.5px;color:#555;text-decoration:none;letter-spacing:.3px;white-space:nowrap}
.nav-link.current{color:#fff}
.nav-link.login{color:#222}
.hero{left:0;top:144px;width:1200px;height:563px;background:linear-gradient(180deg,#6f6b80 0%,#c98a86 30%,#7b7f88 55%,#4d6a3e 80%,#3f5a2c 100%)}
.hero-mask{left:0;top:640px}
.dot{width:10px;height:10px;border-radius:50%}
.h2{font-family:var(--serif);color:var(--blue);font-size:36px;letter-spacing:.5px;font-weight:400}
.offer-list li{list-style:none;position:absolute;left:80px;font-size:14px;color:#555;line-height:25px;width:420px}
.btn{background:linear-gradient(var(--pink-light),var(--pink));color:#fff;font-family:var(--serif);font-size:18px;letter-spacing:1.5px;display:flex;align-items:center;justify-content:center;border:0}
.photo{border-radius:6px}
.band-right{left:0;top:1272px;width:1200px;height:145px;background:linear-gradient(var(--blue-light),var(--blue))}
.band-left{left:0;top:1272px;width:600px;height:145px;background:linear-gradient(var(--pink-light),var(--pink));clip-path:polygon(0 0,558px 0,598px 50%,558px 100%,0 100%)}
.band-title{left:80px;top:1323px;font-family:var(--serif);color:#fff;font-size:33px;white-space:nowrap}
.band-note{left:673px;top:1306px;color:#fff;font-size:19px;white-space:nowrap}
.band-link{left:673px;top:1351px;color:#fff;font-size:17px;font-weight:600;text-decoration:underline}
.svc{text-align:center;width:360px}
.svc h3{font-weight:400;font-size:18px;color:#333;line-height:29px;margin-bottom:18px}
.svc p{font-size:13px;line-height:29px;color:#666}
.testi{left:0;top:1938px;width:1200px;height:479px;background:linear-gradient(180deg,#2a2c2a,#1f241d 60%,#1b2018)}
.testi-title{left:0;width:1200px;top:1988px;text-align:center;font-family:var(--serif);color:#fff;font-size:37px;font-weight:400}
.testi-text{left:240px;width:720px;top:2157px;text-align:center;color:#eee;font-size:18px;line-height:29px}
.testi-name{left:0;width:1200px;top:2277px;text-align:center;color:#fff;font-family:var(--serif);font-size:15px}
.ring{width:12px;height:12px;border-radius:50%;border:2px solid var(--pink)}
.field{background:var(--field);font-size:13px;color:#777;padding:18px 17px}
.footer{left:0;top:2896px;width:1200px;height:229px;background:linear-gradient(var(--blue-light),var(--blue))}
.f-icon{width:62px;height:62px;border-radius:50%;background:rgba(255,255,255,.22);display:flex;align-items:center;justify-content:center}
.f-text{color:#fff;font-size:13.5px;line-height:26px;white-space:nowrap}
.f-rule{left:78px;top:3043px;width:1044px;height:1px;background:rgba(255,255,255,.35)}
.copy{left:80px;top:3076px;color:#fff;font-size:13.5px}
.social{width:14px;height:14px;border-radius:50%;background:#fff}
</style>
</head>
<body>
<header>
  <div class="abs topbar"></div>
  <div class="abs brand">TEBSIRK HOA</div>
  <div class="abs phone-badge"><svg width="20" height="20" viewBox="0 0 24 24"><path fill="#fff" d="M6.6 10.8a15.1 15.1 0 0 0 6.6 6.6l2.2-2.2c.3-.3.7-.4 1-.2 1.1.4 2.3.6 3.6.6.6 0 1 .4 1 1V20c0 .6-.4 1-1 1A17 17 0 0 1 3 4c0-.6.4-1 1-1h3.5c.6 0 1 .4 1 1 0 1.3.2 2.5.6 3.6.1.3 0 .7-.2 1z"/></svg></div>
  <div class="abs phone-num">555 014 2637</div>
  <div class="abs nav-bar"></div>
  <div class="abs nav-home"></div>
  <nav>
    <a class="nav-link current" style="left:108px">HOME</a>
    <a class="nav-link" style="left:188px">SERVICES</a>
    <a class="nav-link" style="left:292px">ORDER RESALE PACKAGE</a>
    <a class="nav-link" style="left:505px">WHY AN HAO WOULD CONTRACT US</a>
    <a class="nav-link" style="left:796px">CONTACT</a>
    <a class="nav-link login" style="left:1078px">LOGIN</a>
  </nav>
</header>

<section>
  <div class="abs hero" role="img" aria-label="City skyline at sunset above a riverside park with a bridge"></div>
  <svg class="abs hero-mask" width="1200" height="68" viewBox="0 0 1200 68">
    <polygon fill="#fff" points="0,12 55,68 0,68"/>
    <polygon fill="#fff" points="1200,12 1145,68 1200,68"/>
    <polygon fill="#fff" points="55,68 240,66 600,54 960,66 1145,68"/>
  </svg>
  <div class="abs dot" style="left:570px;top:692px;background:var(--pink)"></div>
  <div class="abs dot" style="left:592px;top:692px;background:var(--blue)"></div>
  <div class="abs dot" style="left:614px;top:692px;background:var(--blue)"></div>
</section>

<section>
  <h2 class="abs h2" style="left:80px;top:806px">WHAT WE OFFER</h2>
  <ul class="offer-list">
    <li style="top:869px">Accessible, licensed Association Managers</li>
    <li style="top:909px">24 hour Web site access: online account information</li>
    <li style="top:947px">24 hour emergency service</li>
    <li style="top:987px">Provide monthly financial reports to the Board of Directors</li>
    <li style="top:1028px">Read, study and understand all governing documents of the Association.</li>
  </ul>
  <div class="abs btn" style="left:78px;top:1104px;width:187px;height:52px">KNOW MORE</div>
  <div class="abs photo" style="left:612px;top:795px;width:239px;height:343px;background:linear-gradient(#8fb0f0 0%,#c9a58a 35%,#e6dcb8 55%,#3f7a3a 80%,#2c5a2a)" role="img" aria-label="Mediterranean style house with red tile roof and palm trees"></div>
  <div class="abs photo" style="left:883px;top:826px;width:239px;height:344px;background:linear-gradient(#b8a894,#d8c8b8 50%,#ecebe8)" role="img" aria-label="Couple smiling while using a laptop at home"></div>
</section>

<section>
  <div class="abs band-right"></div>
  <div class="abs band-left"></div>
  <div class="abs band-title">LOGIN TO PAY YOUR BILLS</div>
  <div class="abs band-note">homeowners can login and pay their bill</div>
  <div class="abs band-link">LOGIN NOW</div>
</section>

<section>
  <div class="abs svc" style="left:79px;top:1565px">
    <h3>Association Management Services</h3>
    <p>Lorem ipsum dolor sit amet, consectetur adipiscing elit, sed do eiusmod tempor incididunt ut labore et dolore magna aliqua. Ut enim ad minim veniam, quis nostrud exercitation ullamco laboris nisi ut aliquip ex ea commo consequat. Duis aute irure dolor in reprehenderit in voluptate velit esse cillum dolore eu fugiat nulla.</p>
  </div>
  <div class="abs photo" style="left:480px;top:1514px;width:240px;height:323px;background:linear-gradient(160deg,#d6dadc,#8a9aa8 40%,#5d7a56 80%,#4a8a38)" role="img" aria-label="Two colleagues reviewing work on a laptop"></div>
  <div class="abs svc" style="left:764px;top:1565px">
    <h3>TEBSIRK manages communities throughout Southern Nevada</h3>
    <p>Lorem ipsum dolor sit amet, consectetur adipiscing elit, sed do eiusmod tempor incididunt ut labore et dolore magna aliqua. Ut enim ad minim veniam, quis nostrud exercitation ullamco laboris nisi ut aliquip ex ea comm consequat. Duis aute irure dolor in reprehend.</p>
  </div>
</section>

<section>
  <div class="abs testi" role="img" aria-label="Dim evening view of a tiled-roof home behind palm trees"></div>
  <h2 class="abs testi-title">TESTIMONIALS</h2>
  <svg class="abs" style="left:568px;top:2082px" width="64" height="52" viewBox="0 0 64 52">
    <path fill="none" stroke="#ccc" stroke-width="2" d="M28 4C14 8 4 20 4 34a13 13 0 1 0 13-13c-3 0-5 1-6 2 2-8 9-15 18-17zM58 4C44 8 34 20 34 34a13 13 0 1 0 13-13c-3 0-5 1-6 2 2-8 9-15 18-17z"/>
  </svg>
  <p class="abs testi-text">Consectetur adipiscing elit, sed do eiusmod tempor incididunt ut labore et dolore magna aliqua. Ut enim ad minim veniam, quis nostrud exercitation ullamco laboris nisi ut aliquip ex ea commodo consequat. Duis aute irure dolor in reprehe.</p>
  <div class="abs testi-name">- NAME SURNAME</div>
  <div class="abs ring" style="left:562px;top:2332px;background:var(--pink)"></div>
  <div class="abs ring" style="left:582px;top:2332px"></div>
  <div class="abs ring" style="left:603px;top:2332px"></div>
  <div class="abs ring" style="left:624px;top:2332px"></div>
</section>

<section>
  <h2 class="abs h2" style="left:0;width:1200px;text-align:center;top:2468px">GET IN TOUCH</h2>
  <div class="abs field" style="left:78px;top:2548px;width:332px;height:51px">Name</div>
  <div class="abs field" style="left:433px;top:2548px;width:334px;height:51px">Email</div>
  <div class="abs field" style="left:790px;top:2548px;width:332px;height:51px">Phone</div>
  <div class="abs field" style="left:78px;top:2622px;width:1044px;height:113px">Message</div>
  <div class="abs btn" style="left:506px;top:2757px;width:187px;height:51px">SUBMIT</div>
</section>

<footer>
  <div class="abs footer"></div>
  <div class="abs f-icon" style="left:77px;top:2940px"><svg width="20" height="20" viewBox="0 0 24 24"><path fill="#fff" d="M6.6 10.8a15.1 15.1 0 0 0 6.6 6.6l2.2-2.2c.3-.3.7-.4 1-.2 1.1.4 2.3.6 3.6.6.6 0 1 .4 1 1V20c0 .6-.4 1-1 1A17 17 0 0 1 3 4c0-.6.4-1 1-1h3.5c.6 0 1 .4 1 1 0 1.3.2 2.5.6 3.6.1.3 0 .7-.2 1z"/></svg></div>
  <div class="abs f-text" style="left:161px;top:2943px">CALL US<br>555 014 2637</div>
  <div class="abs f-icon" style="left:440px;top:2940px"><svg width="20" height="16" viewBox="0 0 20 16"><rect x="0" y="0" width="20" height="16" rx="2" fill="#fff"/><path d="M1 2l9 7 9-7" fill="none" stroke="#1f9ad2" stroke-width="1.8"/></svg></div>
  <div class="abs f-text" style="left:524px;top:2943px">EMAIL US<br>info@tebsirk_hoa.example</div>
  <div class="abs f-icon" style="left:801px;top:2940px"><svg width="18" height="24" viewBox="0 0 18 24"><path fill="#fff" d="M9 0a9 9 0 0 0-9 9c0 7 9 15 9 15s9-8 9-15a9 9 0 0 0-9-9zm0 12.5A3.5 3.5 0 1 1 9 5.5a3.5 3.5 0 0 1 0 7z"/></svg></div>
  <div class="abs f-text" style="left:886px;top:2943px">Lorem ipsum dolor sit amet,<br>consectetur adipiscing elit.</div>
  <div class="abs f-rule"></div>
  <div class="abs copy">©TEBSIRK HOA- 2019. All Rights Reserved.</div>
  <div class="abs social" style="left:1030px;top:3078px"></div>
  <div class="abs social" style="left:1067px;top:3078px"></div>
  <div class="abs social" style="left:1106px;top:3078px"></div>
</footer>
</body>
</html>
```